Business Card Design Project

Business Card
We are rebranding with a new logo
Industry/Entity Type
Business
Contact Information for Business Card
Dennis Morvale +61 487215963 dennis@quorv.com.au P.O. Box 872 Fernlow QLD 4309
Requirements
Must have
- Logo

```html
<!DOCTYPE html>
<html lang="en">
<head>
<meta charset="utf-8">
<title>Quorv International — Business Card</title>
<link rel="stylesheet" href="https://fonts.googleapis.com/css2?family=Roboto:wght@400;500&family=Roboto+Condensed:wght@700&display=swap">
<style>
  :root {
    --stage: #2b2b2d;
    --paper: #f4f4f4;
    --brand-blue: #0f86be;
    --deep-blue: #0a6a94;
    --glow-blue: #0ba3dc;
    --edge-blue: #065a7c;
    --accent-orange: #ec7d1e;
    --rule: #b4b4b4;
    --ink: #4a4a4a;
    --white: #ffffff;
  }
  * { margin: 0; padding: 0; box-sizing: border-box; }
  html, body {
    width: 1200px; height: 960px; overflow: hidden;
    background: var(--stage);
    font-family: "Roboto", Arial, sans-serif;
  }
  .card {
    position: absolute;
    width: 600px; height: 342px;
    overflow: hidden;
  }
  .card--front { left: 314px; top: 113px; background: var(--paper); }
  .card--back {
    left: 311px; top: 472px;
    background: radial-gradient(ellipse 62% 70% at 50% 40%, var(--glow-blue) 0%, var(--deep-blue) 60%, var(--edge-blue) 100%);
  }
  .brand-name {
    position: absolute;
    font-family: "Roboto Condensed", "Arial Narrow", sans-serif;
    font-weight: 700;
    text-transform: uppercase;
    letter-spacing: 1px;
    line-height: 1;
  }
  .card--front .brand-name {
    right: 39px; top: 92px;
    font-size: 30px;
    color: var(--brand-blue);
    text-align: right;
  }
  .card--back .brand-name {
    left: 0; right: 0; top: 148px;
    font-size: 36px;
    color: var(--white);
    text-align: center;
  }
  .holder-name {
    position: absolute; left: 37px; top: 206px;
    font-family: "Roboto Condensed", "Arial Narrow", sans-serif;
    font-weight: 700; font-size: 20px;
    color: var(--brand-blue);
  }
  .divider {
    position: absolute; left: 37px; top: 238px;
    width: 525px; height: 1px; background: var(--rule);
  }
  .contact-list {
    position: absolute; left: 38px; top: 250px;
    list-style: none;
    font-size: 14px; color: var(--ink); line-height: 19px;
  }
  .contact-list li { display: flex; align-items: center; gap: 8px; }
  .contact-list svg { width: 13px; height: 13px; fill: var(--brand-blue); }
  .postal-address {
    position: absolute; right: 37px; top: 250px;
    font-style: normal; text-align: right;
    font-size: 14px; color: var(--ink); line-height: 19px;
  }
  .footer-bands { position: absolute; left: 0; bottom: 0; width: 600px; height: 36px; }
  .web-address {
    position: absolute; right: 34px; bottom: 9px;
    font-size: 13px; letter-spacing: 2px; color: var(--white);
  }
  .card--back .web-address {
    left: 0; right: 0; bottom: 26px;
    text-align: center; font-size: 14px; letter-spacing: 5px;
  }
</style>
</head>
<body>
  <section class="card card--front" aria-label="Business card front">
    <div class="brand-name">Quorv International</div>
    <h1 class="holder-name">DENNIS MORVALE</h1>
    <div class="divider"></div>
    <ul class="contact-list">
      <li>
        <svg viewBox="0 0 24 24" aria-hidden="true"><path d="M6.6 10.8a15.1 15.1 0 0 0 6.6 6.6l2.2-2.2c.3-.3.7-.4 1-.2 1.1.4 2.3.6 3.6.6.6 0 1 .4 1 1V20c0 .6-.4 1-1 1A17 17 0 0 1 3 4c0-.6.4-1 1-1h3.5c.6 0 1 .4 1 1 0 1.3.2 2.5.6 3.6.1.3 0 .7-.2 1z"/></svg>
        +61 487215963
      </li>
      <li>
        <svg viewBox="0 0 24 24" aria-hidden="true"><path d="M2 5h20v2l-10 6L2 7z M2 9l10 6 10-6v10H2z"/></svg>
        dennis@quorv.com.au
      </li>
    </ul>
    <address class="postal-address">P.O. Box 872<br>Fernlow QLD 4309</address>
    <svg class="footer-bands" viewBox="0 0 600 36" aria-hidden="true">
      <rect x="0" y="13" width="362" height="8" fill="var(--accent-orange)"/>
      <rect x="0" y="21" width="600" height="15" fill="var(--brand-blue)"/>
      <polygon points="374,0 600,0 600,36 352,36" fill="var(--deep-blue)"/>
    </svg>
    <div class="web-address">www.quorv.com.au</div>
  </section>

  <section class="card card--back" aria-label="Business card back">
    <div class="brand-name">Quorv International</div>
    <div class="web-address">www.quorv.com.au</div>
  </section>
</body>
</html>
```